New florist business website design

Number 1 want is an easy to navigate & check out website
Needs to be beautiful and eye catching as well.
This is an online only business (no shop front)
Rustic and blush pinks, neutrals, woods, leaves
Customers need to be able to go onto my website, select something they want to buy but have the option to use a drop down box to change colours of the flowers, or add notes to make changes to the arrangement

Industry/Entity Type

Florist

Coding

Coded - Design and coding required

Number of Pages Required

5+ page

Colors
f9d9e8
fff2ec
fffefc

Requirements
Must have
• Drop down menu to take you to other pages for Arrangements, bouquets, everlasting arrangements, gifts, contact
Be able to purchase and “add to basket”
Checkout page
Nice to have
• Be able to add my own photos once I’ve taken new ones
Should not have
• Tacky images or clip art

```html
<!DOCTYPE html>
<html lang="en">
<head>
<meta charset="utf-8">
<title>Fern &amp; Fable — Florist</title>
<link rel="stylesheet" href="https://fonts.googleapis.com/css2?family=Playfair+Display:wght@400;500;600&family=Roboto:wght@300;400;500&family=Great+Vibes&display=swap">
<style>
:root{
  --blush:#f9d9e8;
  --peach:#fff2ec;
  --cream:#fffefc;
  --pink:#e8479a;
  --ink:#1d1d1d;
  --muted:#444;
  --gold:#f2b600;
  --grey-tile:#f1f1f1;
  --serif:'Playfair Display',Georgia,serif;
  --sans:'Roboto',Arial,sans-serif;
  --script:'Great Vibes',cursive;
}
*{box-sizing:border-box;margin:0;padding:0}
html,body{width:1200px;height:4640px;overflow:hidden;background:var(--cream);color:var(--ink);font-family:var(--sans)}
.page{position:relative;width:1200px;height:4640px;overflow:hidden}
.abs{position:absolute}

/* top bar */
.topbar{top:0;left:0;width:1200px;height:40px;background:var(--peach);display:flex;align-items:center;justify-content:space-between;padding:0 60px 0 98px;font-size:13px;font-weight:500}
.topbar .ship{display:flex;align-items:center;gap:8px}
.topbar .util{display:flex;gap:36px;text-transform:uppercase;font-size:13px}
.topbar .util span{display:flex;align-items:center;gap:6px}

/* nav */
.nav{top:40px;left:0;width:1200px;height:104px;display:flex;align-items:center;font-family:var(--serif);font-size:15px;color:#333}
.nav .left{position:absolute;left:160px;display:flex;gap:36px}
.nav .right{position:absolute;left:698px;display:flex;gap:36px}
.nav .brand{position:absolute;left:550px;width:110px;text-align:center;font-family:var(--serif);font-size:21px;color:#777;top:32px}
.nav .brand::before{content:"";position:absolute;left:10px;top:-16px;width:90px;height:90px;border:1px solid #ddd;border-radius:50%}
.caret::after{content:"";display:inline-block;margin-left:5px;width:5px;height:5px;border-right:1.3px solid #333;border-bottom:1.3px solid #333;transform:translateY(-3px) rotate(45deg)}

/* hero */
.hero{top:144px;left:0;width:1200px;height:648px;background:
  radial-gradient(ellipse at 50% 30%,#e0702d 0 14%,transparent 30%),
  radial-gradient(ellipse at 88% 40%,#b5141c 0 10%,transparent 24%),
  radial-gradient(ellipse at 6% 30%,#f0b020 0 10%,transparent 22%),
  linear-gradient(180deg,#3a4036 0%,#5a3a32 55%,#f4eeee 86%,#fffefc 100%)}
.hero h1{position:absolute;top:330px;width:100%;text-align:center;font-family:var(--serif);font-weight:600;font-size:72px;line-height:64px;color:#fff}
.btn{display:inline-flex;align-items:center;justify-content:center;background:var(--pink);color:#fff;font-family:var(--serif);font-weight:600;font-size:15px}
.hero .btn{position:absolute;left:526px;top:490px;width:145px;height:44px}

/* section titles */
.kicker{width:1200px;left:0;text-align:center;font-size:21px;font-weight:300;color:#222}
.title{width:1200px;left:0;text-align:center;font-family:var(--serif);font-weight:500;font-size:44px}
.lede{left:250px;width:700px;text-align:center;font-size:14px;line-height:26px;color:#222}

/* occasions */
.occasions{left:99px;top:1035px;display:grid;grid-template-columns:repeat(4,238px);column-gap:16px;row-gap:16px}
.occasion{height:310px;display:flex;flex-direction:column}
.occasion .ph{height:263px}
.occasion .label{flex:1;background:var(--blush);display:flex;align-items:center;justify-content:center;font-weight:500;font-size:18px;letter-spacing:.3px}

/* join */
.join{top:1762px;left:0;width:1200px;height:306px;background:var(--peach)}
.join .field{position:absolute;top:189px;height:45px;background:#fff;font-size:13px;display:flex;align-items:center;padding-left:16px;color:#222}
.join .btn{position:absolute;top:189px;left:855px;width:148px;height:45px;font-size:16px}

/* products */
.products{left:99px;top:2248px;display:grid;grid-template-columns:repeat(4,238px);column-gap:16px;row-gap:16px}
.product{height:316px;background:#fff;box-shadow:0 0 6px rgba(0,0,0,.12);padding:6px;display:flex;flex-direction:column;align-items:center}
.product .ph{width:100%;height:176px;background:var(--grey-tile);position:relative}
.product .ph i{position:absolute;left:50%;top:50%;width:110px;height:140px;transform:translate(-50%,-50%);border-radius:50% 50% 20% 20%}
.product .name{margin-top:16px;font-size:13px;text-transform:uppercase}
.stars{color:var(--gold);font-size:12px;letter-spacing:1px;margin-top:5px}
.product .price{font-family:var(--serif);font-size:15px;margin-top:5px}
.product .buy{margin-top:auto;margin-bottom:4px;width:100%;display:flex;gap:8px;padding:0 2px}
.select{width:96px;height:32px;border:1px solid #e5e5e5;display:flex;align-items:center;padding-left:6px;font-size:9px;color:#555;gap:6px}
.select .sw{margin-left:auto;width:16px;height:16px;background:#e2001a}
.select .ar{width:0;height:0;border-left:4px solid transparent;border-right:4px solid transparent;border-top:5px solid #333;margin-right:6px}
.product .btn{flex:1;height:32px;font-size:12px;background:var(--blush);color:#b0357a}

/* deal */
.deal{top:2990px;left:0;width:1200px;height:400px;background:linear-gradient(90deg,#f4b3c4 0%,#fbdfe6 22%,#fde8ed 50%,#fbdfe6 78%,#f4b3c4 100%)}
.deal .flowers-l{position:absolute;left:0;top:0;width:330px;height:400px;background:radial-gradient(ellipse at 40% 45%,#ee7d9c 0 30%,#6a8f3c 55%,transparent 72%)}
.deal .flowers-r{position:absolute;right:0;top:40px;width:240px;height:360px;background:radial-gradient(ellipse at 60% 60%,#ee7d9c 0 30%,#6a8f3c 55%,transparent 72%)}
.deal .script{position:absolute;top:80px;width:100%;text-align:center;left:80px;font-family:var(--script);font-size:46px;color:#222}
.deal .sub{position:absolute;top:150px;width:100%;text-align:center;left:80px;font-family:var(--serif);font-size:30px}
.deal .off{position:absolute;top:200px;width:100%;text-align:center;left:80px;font-family:var(--serif);font-weight:600;font-size:50px}
.deal .btn{position:absolute;left:608px;top:300px;width:145px;height:42px}

/* testimonials */
.reviews{left:97px;top:3586px;display:grid;grid-template-columns:repeat(4,240px);column-gap:14px}
.review{text-align:center}
.review .ph{height:278px}
.review .who{margin-top:14px;font-weight:500;font-size:15px;text-transform:uppercase}
.review .stars{font-size:15px;margin-top:4px}
.review q{display:block;margin-top:6px;font-style:italic;font-size:11px;line-height:19px;color:#333;padding:0 4px}

/* footer */
.footer{top:4070px;left:0;width:1200px;height:264px;background:var(--peach)}
.fcol{position:absolute;top:54px;width:220px;text-align:center}
.fcol h4{font-weight:500;font-size:19px;text-decoration:underline;text-underline-offset:4px;margin-bottom:12px}
.fcol li{list-style:none;font-size:14px;line-height:26px;color:#222}
.social{position:absolute;top:194px;left:500px;display:flex;gap:6px}
.social span{width:32px;height:32px;border-radius:50%;background:#111}
.strip{top:4334px;left:0;width:1200px;height:238px;display:grid;grid-template-columns:repeat(6,200px)}
.strip .insta{position:absolute;left:567px;top:10px;width:26px;height:26px;border:2px solid #fff;border-radius:50%}
.copyright{top:4572px;left:0;width:1200px;height:68px;background:var(--peach);display:flex;align-items:center;justify-content:center;font-size:14px}
</style>
</head>
<body>
<div class="page">

  <div class="abs topbar">
    <div class="ship">
      <svg width="22" height="14" viewBox="0 0 22 14" fill="none" stroke="#111" stroke-width="1.3"><rect x="1" y="1" width="13" height="9"/><path d="M14 4h4l3 3v3h-7"/><circle cx="5" cy="11.5" r="1.6" fill="#fff"/><circle cx="17" cy="11.5" r="1.6" fill="#fff"/></svg>
      Complimentary Shipping On domestic orders over $50
    </div>
    <div class="util">
      <span><svg width="12" height="13" viewBox="0 0 12 13" fill="none" stroke="#111" stroke-width="1.2"><circle cx="6" cy="4" r="3"/><path d="M1 12c0-3 2.5-4.5 5-4.5s5 1.5 5 4.5"/></svg>My Account</span>
      <span><svg width="12" height="13" viewBox="0 0 12 13" fill="none" stroke="#111" stroke-width="1.2"><rect x="1" y="4" width="10" height="8"/><path d="M3.5 4V2.5a2.5 2.5 0 0 1 5 0V4"/></svg>Cart</span>
      <span><svg width="13" height="13" viewBox="0 0 13 13" fill="none" stroke="#111" stroke-width="1.2"><circle cx="7.5" cy="5.5" r="4.3"/><path d="M4.5 8.5 1 12"/></svg>Search</span>
    </div>
  </div>

  <nav class="abs nav">
    <div class="left"><span class="caret">Home</span><span class="caret">Arrangements</span><span class="caret">Bouquets</span></div>
    <div class="brand">Fern &amp; Fable</div>
    <div class="right"><span class="caret">Everlasting arrangements</span><span class="caret">Gifts</span><span>Contact</span></div>
  </nav>

  <section class="abs hero" role="img" aria-label="Overhead photo of a wrapped bouquet of orange and red roses surrounded by berries and blooms">
    <h1>Live in moments<br>that matter.</h1>
    <a class="btn">Shop Now</a>
  </section>

  <p class="abs kicker" style="top:830px">Roses, Flowers, Plants &amp; Gifts To</p>
  <h2 class="abs title" style="top:862px">Shop Our Occasion</h2>
  <p class="abs lede" style="top:924px">Lorem ipsum dolor sit amet, consectetur adipiscing elit, sed do eiusmod tempor incididunt ut labore et dolore magna aliqua. Quis ipsum suspendisse ultrices gravida. Risus commodo viverra maecenas accumsan lacus vel facilisis.</p>

  <div class="abs occasions">
    <div class="occasion"><div class="ph" role="img" aria-label="Wreath of pale green and pink flowers" style="background:radial-gradient(circle,#5a5a3e 0 18%,#c9d8a8 30%,#e9b8c4 42%,#4c4a36 60%)"></div><div class="label">SYMPATHY</div></div>
    <div class="occasion"><div class="ph" role="img" aria-label="Hat box of yellow roses and macarons" style="background:linear-gradient(180deg,#e8c84a 0%,#c99ab0 40%,#f1e3e3 70%,#b7967a 100%)"></div><div class="label">BIRTHDAY</div></div>
    <div class="occasion"><div class="ph" role="img" aria-label="Bouquet of deep red roses" style="background:radial-gradient(ellipse at 50% 45%,#a2162a 0 40%,#7a1c22 60%,#c0402e 100%)"></div><div class="label">LOVE &amp; ROMANCE</div></div>
    <div class="occasion"><div class="ph" role="img" aria-label="Vase of white hydrangea with baby's breath" style="background:linear-gradient(180deg,#4a3a2e 0%,#efe4e2 35%,#d7a4b0 65%,#5a4636 100%)"></div><div class="label">ANNIVERSARY</div></div>
    <div class="occasion"><div class="ph" role="img" aria-label="Lilac bouquet with balloons" style="background:linear-gradient(135deg,#c4b3d8 0%,#f0e7f2 45%,#a287b8 100%)"></div><div class="label">NEW BABY</div></div>
    <div class="occasion"><div class="ph" role="img" aria-label="White roses in a gold vase" style="background:linear-gradient(180deg,#f5f3ee 0%,#e8e6de 45%,#c4a640 75%,#efeae0 100%)"></div><div class="label">CONGRATULATIONS</div></div>
    <div class="occasion"><div class="ph" role="img" aria-label="Pink and burgundy bouquet on a wooden table" style="background:linear-gradient(180deg,#ececec 0%,#d68a9a 40%,#8a2e46 60%,#4a3628 100%)"></div><div class="label">THANKS</div></div>
    <div class="occasion"><div class="ph" role="img" aria-label="Wrapped bouquet of peach and pink roses" style="background:linear-gradient(135deg,#f0b8c8 0%,#f4a27e 45%,#e44a6a 70%,#f8d8e2 100%)"></div><div class="label">GETWELL</div></div>
  </div>

  <section class="abs join">
    <h2 class="abs title" style="top:56px;font-size:38px">Join the Fern &amp; Fable</h2>
    <p class="abs lede" style="top:114px">Lorem ipsum dolor sit amet, consectetur adipiscing elit, sed do eiusmod tempor incididunt ut labore et dolore magna aliqua. Quis ipsum suspendisse ultrices gravida.</p>
    <div class="field" style="left:196px;width:320px">Full Name</div>
    <div class="field" style="left:526px;width:320px">Email Address</div>
    <a class="btn">Sign Up!</a>
  </section>

  <p class="abs kicker" style="top:2133px">Roses, Flowers, Plants &amp; Gifts To</p>
  <h2 class="abs title" style="top:2164px">Featured Products</h2>

  <div class="abs products">
    <div class="product"><div class="ph" role="img" aria-label="Lilies and roses in a red vase"><i style="background:radial-gradient(circle,#e8452c 0 40%,#f29a3a 60%,transparent 72%)"></i></div><p class="name">Spring Fling Tulip Vase</p><p class="stars">★★★★★</p><p class="price">$ 49.99</p><div class="buy"><div class="select">Choose Color<span class="sw"></span><span class="ar"></span></div><a class="btn">Add To Cart</a></div></div>
    <div class="product"><div class="ph" role="img" aria-label="Pink roses in a glass cube"><i style="background:radial-gradient(circle,#e9749e 0 40%,#8c3a6e 60%,transparent 72%)"></i></div><p class="name">Spring Fling Tulip Vase</p><p class="stars">★★★★★</p><p class="price">$ 49.99</p><div class="buy"><div class="select">Choose Color<span class="sw"></span><span class="ar"></span></div><a class="btn">Add To Cart</a></div></div>
    <div class="product"><div class="ph" role="img" aria-label="Pastel flowers in a basket"><i style="background:radial-gradient(circle,#eef0d6 0 40%,#d9b2d4 60%,transparent 72%)"></i></div><p class="name">Spring Fling Tulip Vase</p><p class="stars">★★★★★</p><p class="price">$ 49.99</p><div class="buy"><div class="select">Choose Color<span class="sw"></span><span class="ar"></span></div><a class="btn">Add To Cart</a></div></div>
    <div class="product"><div class="ph" role="img" aria-label="Mixed tulips in a glass vase"><i style="background:radial-gradient(circle,#e63a3a 0 30%,#f3c22a 50%,#7a3ea0 62%,transparent 72%)"></i></div><p class="name">Spring Fling Tulip Vase</p><p class="stars">★★★★★</p><p class="price">$ 49.99</p><div class="buy"><div class="select">Choose Color<span class="sw"></span><span class="ar"></span></div><a class="btn">Add To Cart</a></div></div>
    <div class="product"><div class="ph" role="img" aria-label="Green orchids in a tall vase"><i style="background:radial-gradient(circle,#b9d44a 0 40%,#5f7f3a 60%,transparent 72%)"></i></div><p class="name">Spring Fling Tulip Vase</p><p class="stars">★★★★★</p><p class="price">$ 49.99</p><div class="buy"><div class="select">Choose Color<span class="sw"></span><span class="ar"></span></div><a class="btn">Add To Cart</a></div></div>
    <div class="product"><div class="ph" role="img" aria-label="Orange and white roses in a vase"><i style="background:radial-gradient(circle,#f4f0e0 0 30%,#f08a2c 55%,transparent 72%)"></i></div><p class="name">Spring Fling Tulip Vase</p><p class="stars">★★★★★</p><p class="price">$ 49.99</p><div class="buy"><div class="select">Choose Color<span class="sw"></span><span class="ar"></span></div><a class="btn">Add To Cart</a></div></div>
    <div class="product"><div class="ph" role="img" aria-label="Purple and pink flowers in a red vase"><i style="background:radial-gradient(circle,#c73a74 0 35%,#7a3ea0 58%,transparent 72%)"></i></div><p class="name">Spring Fling Tulip Vase</p><p class="stars">★★★★★</p><p class="price">$ 49.99</p><div class="buy"><div class="select">Choose Color<span class="sw"></span><span class="ar"></span></div><a class="btn">Add To Cart</a></div></div>
    <div class="product"><div class="ph" role="img" aria-label="Purple and lilac flowers in a blue vase"><i style="background:radial-gradient(circle,#9a7ad0 0 40%,#5a3a9a 60%,transparent 72%)"></i></div><p class="name">Spring Fling Tulip Vase</p><p class="stars">★★★★★</p><p class="price">$ 49.99</p><div class="buy"><div class="select">Choose Color<span class="sw"></span><span class="ar"></span></div><a class="btn">Add To Cart</a></div></div>
  </div>

  <section class="abs deal">
    <div class="flowers-l" role="img" aria-label="Pink roses and leaves"></div>
    <div class="flowers-r" role="img" aria-label="Pink roses and white blooms"></div>
    <p class="script">Deal of the day</p>
    <p class="sub">Standard Lorem Ipsum sage, used</p>
    <p class="off">50% Off</p>
    <a class="btn">Shop Now</a>
  </section>

  <p class="abs kicker" style="top:3469px">Roses, Flowers, Plants &amp; Gifts To</p>
  <h2 class="abs title" style="top:3500px">Client Testimonials</h2>

  <div class="abs reviews">
    <div class="review"><div class="ph" role="img" aria-label="Two customers in flower crowns holding bouquets" style="background:linear-gradient(180deg,#6a7a4a 0%,#d8c2a8 40%,#8a3e4a 75%,#3a3a2e 100%)"></div><p class="who">Ella Moore</p><p class="stars">★★★★★</p><q>Lorem ipsum dolor sit amet, ctur adipiscing elit, sed do eiusmod tempor incididunt ut labore et dolore magna aliqua</q></div>
    <div class="review"><div class="ph" role="img" aria-label="Mauve roses in a white vase" style="background:linear-gradient(180deg,#e8e8e8 0%,#c9a0b6 45%,#f4f4f2 80%)"></div><p class="who">Ella Moore</p><p class="stars">★★★★★</p><q>Lorem ipsum dolor sit amet, ctur adipiscing elit, sed do eiusmod tempor incididunt ut labore et dolore magna aliqua</q></div>
    <div class="review"><div class="ph" role="img" aria-label="Customer holding a large bouquet outdoors" style="background:linear-gradient(180deg,#5a6a3e 0%,#efe2cf 45%,#3a3a3a 100%)"></div><p class="who">Ella Moore</p><p class="stars">★★★★★</p><q>Lorem ipsum dolor sit amet, ctur adipiscing elit, sed do eiusmod tempor incididunt ut labore et dolore magna aliqua</q></div>
    <div class="review"><div class="ph" role="img" aria-label="Bouquet of red and pink flowers held in hand" style="background:linear-gradient(180deg,#f2f0ee 0%,#c8283e 45%,#e07890 70%,#f0ebe6 100%)"></div><p class="who">Ella Moore</p><p class="stars">★★★★★</p><q>Lorem ipsum dolor sit amet, ctur adipiscing elit, sed do eiusmod tempor incididunt ut labore et dolore magna aliqua</q></div>
  </div>

  <footer class="abs footer">
    <div class="fcol" style="left:90px"><h4>ABOUT</h4><ul><li>Our Story</li><li>Brands</li><li>Shop</li><li>About US</li></ul></div>
    <div class="fcol" style="left:463px"><h4>SUPPORT</h4><ul><li>FAQ</li><li>Contact Us</li><li>Press</li></ul></div>
    <div class="fcol" style="left:859px"><h4>INFO</h4><ul><li>Privacy Policy</li><li>Terms Of Services</li><li>Track Order</li><li>Join Us</li></ul></div>
    <div class="social" aria-label="Social links"><span></span><span></span><span></span><span></span></div>
  </footer>

  <div class="abs strip">
    <div role="img" aria-label="White flowers in a basket" style="background:linear-gradient(180deg,#3a4a52,#d8dcd8,#4a4e50)"></div>
    <div role="img" aria-label="Red and white bouquet" style="background:linear-gradient(180deg,#4a3a30,#c8302e,#eae6e0)"></div>
    <div role="img" aria-label="Dark red roses" style="background:linear-gradient(180deg,#3a2a2a,#8a2a36,#5a4038)"></div>
    <div role="img" aria-label="Customers with flower crowns" style="background:linear-gradient(180deg,#6a6a4a,#d8b4a0,#2e2e34)"></div>
    <div role="img" aria-label="Pastel roses" style="background:linear-gradient(180deg,#b0a8a0,#d89aa8,#8a7a70)"></div>
    <div role="img" aria-label="Orange and pink flowers in a jar" style="background:linear-gradient(180deg,#f4f2ee,#e06a4a,#f0e8e0)"></div>
    <span class="insta" aria-hidden="true"></span>
  </div>

  <div class="abs copyright">Copyright © 2021 Fern &amp; Fable. All rights reserved.</div>
</div>
</body>
</html>
```